Stationery Design Task - Stationary, memo and report templates for professional services company

Looking for someone to update stationary design but just as importantly come up with a template for reports and memos for use in our consulting firm. Would also like some brand use guidelines to be able to share with our whole team. We have an existing logo that we like. Need to update with a more contemporary look so that our deliverables to clients look good and professional yet stylish. This is for business to business communications. No need for envelope design. Important to have design for multiple pages, i.e. first page of a report and then 2nd page. Need to use in MS word documents so must be easy to use and replicate. Don't want something overly complex. Clean, fresh looking is best.

Industry/Entity Type

Information Technology

Font styles to use
Sans Serif

Colors
33a6d7
0792cd
85cae6
cee9f5
cedeed
85abd2
3377b5
0455a3

Requirements
Must have
• Clean look but with a little style or pop. Something that can easily be used in word documents. Need to have page styles that have a first page of a report (not a cover page) and then secondary page.
Nice to have
• - Although the dark blue is our primary color. Might be willing to look at some accent color as well.
Should not have
• Not just our logo on the page with a color bar.

```html
<!DOCTYPE html>
<html lang="en">
<head>
<meta charset="utf-8">
<title>Northvale Systems – Stationery Set</title>
<link rel="stylesheet" href="https://fonts.googleapis.com/css2?family=Roboto:wght@300;400;500;700;900&display=swap">
<style>
  :root {
    --stage: #676767;
    --paper-top: #ffffff;
    --paper-bottom: #c9c9c9;
    --blue: #0792cd;
    --blue-mid: #33a6d7;
    --blue-deep: #0455a3;
    --blue-soft: #85cae6;
    --ink: #4a4a4a;
    --ink-soft: #6d6d6d;
    --rule: #7a7a7a;
  }
  * { box-sizing: border-box; margin: 0; padding: 0; }
  html, body { width: 932px; height: 1200px; overflow: hidden; }
  body {
    background: var(--stage);
    font-family: "Roboto", Arial, sans-serif;
    position: relative;
  }
  .page {
    position: absolute;
    width: 381px;
    height: 536px;
    background: linear-gradient(180deg, var(--paper-top) 0%, var(--paper-bottom) 100%);
    overflow: hidden;
    box-shadow: 0 1px 3px rgba(0,0,0,.35);
  }
  .page--cover   { left: 62px;  top: 50px; }
  .page--contents{ left: 485px; top: 50px; }
  .page--letter  { left: 64px;  top: 620px; }
  .page--follow  { left: 483px; top: 620px;
    background: linear-gradient(90deg, #d2d2d2 0%, #ffffff 100%); }

  .brand {
    position: absolute;
    display: flex;
    align-items: center;
    gap: 8px;
    color: var(--blue);
    font-weight: 700;
    white-space: nowrap;
  }
  .brand__dot { border-radius: 50%; background: var(--blue); flex: none; }

  /* Cover */
  .cover__pattern { position: absolute; right: 0; top: 0; }
  .page--cover .brand { left: 58px; top: 170px; font-size: 30px; }
  .page--cover .brand__dot { width: 34px; height: 34px; }
  .cover__title {
    position: absolute; left: 0; right: 0; top: 284px;
    text-align: center; font-weight: 900; font-size: 39px;
    color: var(--blue); letter-spacing: .5px;
  }
  .cover__subtitle {
    position: absolute; left: 109px; width: 158px; top: 381px;
    border-top: 1px solid var(--rule); border-bottom: 1px solid var(--rule);
    padding: 3px 0 2px; text-align: center;
    font-weight: 700; font-size: 16px; color: var(--ink-soft);
  }
  .cover__date {
    position: absolute; left: 0; right: 0; top: 453px;
    text-align: center; font-weight: 500; font-size: 14px; color: var(--blue);
  }

  /* Contents */
  .contents__heading {
    position: absolute; left: 30px; top: 40px; width: 321px;
    font-size: 17px; font-weight: 400; color: var(--blue);
    padding-bottom: 6px; border-bottom: 1px solid var(--rule);
  }
  .contents__list { position: absolute; left: 30px; top: 78px; width: 309px; list-style: none; }
  .contents__item {
    display: flex; align-items: baseline; height: 16.25px;
    font-size: 10px; font-weight: 300; color: var(--ink);
  }
  .contents__item--section { color: var(--blue); font-weight: 500; }
  .contents__label { white-space: nowrap; }
  .contents__leader {
    flex: 1; margin: 0 4px; border-bottom: 1px dotted #8a8a8a; transform: translateY(-3px);
  }
  .contents__page { color: var(--ink); font-weight: 300; width: 12px; text-align: right; }

  .wave-band { position: absolute; left: 0; bottom: 0; width: 100%; }

  /* Letter */
  .page--letter .brand { left: 103px; top: 38px; font-size: 22px; }
  .page--letter .brand__dot { width: 24px; height: 24px; }
  .letter__greeting {
    position: absolute; left: 33px; top: 151px; font-size: 10px; font-weight: 300; color: var(--ink);
  }
  .letter__body { position: absolute; left: 33px; top: 178px; width: 316px; }
  .letter__body p {
    font-size: 5.6px; line-height: 8.2px; font-weight: 300; color: var(--ink);
    margin-bottom: 8px; text-align: justify;
  }
  .letter__closing {
    position: absolute; left: 33px; top: 352px; font-size: 5.6px; font-weight: 300; color: var(--ink);
  }
  .letter__signature { position: absolute; left: 31px; top: 372px; }
  .letter__footer {
    position: absolute; left: 0; top: 497px; width: 100%; height: 17px;
    background: var(--blue); color: #fff; font-size: 6.4px; font-weight: 500;
    display: flex; align-items: center; justify-content: center; gap: 10px; letter-spacing: .1px;
  }

  /* Follow-on page */
  .page--follow .brand { right: 28px; top: 493px; font-size: 9px; gap: 4px; }
  .page--follow .brand__dot { width: 12px; height: 12px; }
</style>
</head>
<body>

<!-- Report cover -->
<section class="page page--cover">
  <svg class="cover__pattern" width="381" height="150" viewBox="0 0 381 150" role="img" aria-label="Cluster of blue hexagon tiles in the top right corner">
    <defs>
      <linearGradient id="coverBlue" x1="0" y1="0" x2="1" y2="1">
        <stop offset="0" stop-color="#33a6d7"/>
        <stop offset="1" stop-color="#0455a3"/>
      </linearGradient>
    </defs>
    <polygon fill="url(#coverBlue)" points="55,0 381,0 381,142 360,142 338,110 320,92 290,84 250,78 215,66 180,78 148,80 126,62 95,42"/>
  </svg>

  <div class="brand"><span class="brand__dot"></span>Northvale Systems</div>
  <h1 class="cover__title">SLATE HARBOR</h1>
  <p class="cover__subtitle">IT SUPPORT GUIDE</p>
  <p class="cover__date">SEBTEMBER 2018</p>
</section>

<!-- Table of contents -->
<section class="page page--contents">
  <h2 class="contents__heading">Table of content</h2>
  <ul class="contents__list">
    <li class="contents__item contents__item--section"><span class="contents__label">What's New</span><span class="contents__leader"></span><span class="contents__page">2</span></li>
    <li class="contents__item"><span class="contents__label">Proin pede metus, vulputate nec, fermentum fringil</span><span class="contents__leader"></span><span class="contents__page">2</span></li>
    <li class="contents__item contents__item--section"><span class="contents__label">Vehicula</span><span class="contents__leader"></span><span class="contents__page">5</span></li>
    <li class="contents__item"><span class="contents__label">Vitae, justo.d</span><span class="contents__leader"></span><span class="contents__page">5</span></li>
    <li class="contents__item"><span class="contents__label">Etiam neque. Fusce</span><span class="contents__leader"></span><span class="contents__page">5</span></li>
    <li class="contents__item contents__item--section"><span class="contents__label">Tellus odio, d</span><span class="contents__leader"></span><span class="contents__page">8</span></li>
    <li class="contents__item"><span class="contents__label">apibus id ferment</span><span class="contents__leader"></span><span class="contents__page">8</span></li>
    <li class="contents__item contents__item--section"><span class="contents__label">Um quis, suscipit id ers</span><span class="contents__leader"></span><span class="contents__page">10</span></li>
    <li class="contents__item"><span class="contents__label">Duis pulvinar. Etiam</span><span class="contents__leader"></span><span class="contents__page">10</span></li>
    <li class="contents__item"><span class="contents__label">egestas wisi a erat. Vi</span><span class="contents__leader"></span><span class="contents__page">10</span></li>
    <li class="contents__item contents__item--section"><span class="contents__label">Vamus luctus egestas</span><span class="contents__leader"></span><span class="contents__page">15</span></li>
    <li class="contents__item"><span class="contents__label">leo. Aenean vel massa</span><span class="contents__leader"></span><span class="contents__page">15</span></li>
    <li class="contents__item contents__item--section"><span class="contents__label">Quis mauris vehicula</span><span class="contents__leader"></span><span class="contents__page">17</span></li>
    <li class="contents__item"><span class="contents__label">lacinia. Nullam at arcu</span><span class="contents__leader"></span><span class="contents__page">18</span></li>
    <li class="contents__item contents__item--section"><span class="contents__label">a est sollicitudin euism</span><span class="contents__leader"></span><span class="contents__page">18</span></li>
    <li class="contents__item"><span class="contents__label">od. Et harum quidem r</span><span class="contents__leader"></span><span class="contents__page">22</span></li>
    <li class="contents__item"><span class="contents__label">erum facilis est et exp</span><span class="contents__leader"></span><span class="contents__page">22</span></li>
    <li class="contents__item"><span class="contents__label">edita distinctio. Nulla</span><span class="contents__leader"></span><span class="contents__page">22</span></li>
    <li class="contents__item contents__item--section"><span class="contents__label">turpis magna, cursus s</span><span class="contents__leader"></span><span class="contents__page">23</span></li>
    <li class="contents__item"><span class="contents__label">it amet, suscipit a, int</span><span class="contents__leader"></span><span class="contents__page">23</span></li>
    <li class="contents__item"><span class="contents__label">erdum id, felis. Sed ac</span><span class="contents__leader"></span><span class="contents__page">25</span></li>
    <li class="contents__item"><span class="contents__label">dolor sit amet purus m</span><span class="contents__leader"></span><span class="contents__page">25</span></li>
    <li class="contents__item contents__item--section"><span class="contents__label">alesuada congue.Cur</span><span class="contents__leader"></span><span class="contents__page">27</span></li>
    <li class="contents__item"><span class="contents__label">abitur sagittis hendreri</span><span class="contents__leader"></span><span class="contents__page">27</span></li>
    <li class="contents__item"><span class="contents__label">t ante. In rutrum. Nulla</span><span class="contents__leader"></span><span class="contents__page">27</span></li>
  </ul>

  <svg class="wave-band" width="381" height="44" viewBox="0 0 381 44" role="img" aria-label="Band of blue hexagon tiles along the bottom edge">
    <defs>
      <linearGradient id="bandBlue" x1="0" y1="0" x2="0" y2="1">
        <stop offset="0" stop-color="#33a6d7"/>
        <stop offset="1" stop-color="#0792cd"/>
      </linearGradient>
    </defs>
    <polygon fill="url(#bandBlue)" points="0,14 60,14 75,2 120,2 140,14 200,12 215,6 270,0 320,4 381,0 381,44 0,44"/>
  </svg>
</section>

<!-- Letterhead -->
<section class="page page--letter">
  <div class="brand"><span class="brand__dot"></span>Northvale Systems</div>
  <p class="letter__greeting">Dear Mr. Carter,</p>
  <div class="letter__body">
    <p>Thank you for choosing our team to support your office network this year. This letter confirms the scope of services, the response times agreed during our meeting, and the contacts who will handle your requests from the first week onward.</p>
    <p>Our engineers will review every workstation, server and backup routine before the handover. Any issues we find will be logged, ranked by urgency and shared with you in a short weekly report so that nothing is missed.</p>
    <p>Remote support is available on weekdays from eight until six, with on-site visits booked within one working day. Urgent outages outside these hours are covered by our standby line, and every call is recorded in your service history.</p>
    <p>Please review the enclosed guide and let us know if any details need to change. We look forward to working with you.</p>
  </div>
  <p class="letter__closing">Sincerely,</p>
  <svg class="letter__signature" width="72" height="30" viewBox="0 0 72 30" role="img" aria-label="Handwritten signature of Daniel Carter">
    <rect width="72" height="30" rx="4" fill="#85abd2" opacity=".35"/>
  </svg>

  <svg class="wave-band" width="381" height="66" viewBox="0 0 381 66" role="img" aria-label="Band of blue hexagon tiles along the bottom edge">
    <defs>
      <linearGradient id="letterBlue" x1="0" y1="0" x2="0" y2="1">
        <stop offset="0" stop-color="#33a6d7"/>
        <stop offset="1" stop-color="#0792cd"/>
      </linearGradient>
    </defs>
    <polygon fill="url(#letterBlue)" points="0,14 40,14 55,2 110,2 135,12 180,12 200,0 260,0 290,10 340,10 381,0 381,66 0,66"/>
  </svg>
  <div class="letter__footer">
    <span>1420 HARLOW STREET, BRIDGEPORT, OREGON 97120</span>
    <span>555 210 4473 | INFO@NORTHVALESYSTEMS.COM</span>
  </div>
</section>

<!-- Continuation page -->
<section class="page page--follow">
  <div class="brand"><span class="brand__dot"></span>Northvale</div>
</section>

</body>
</html>
```